Packaging design for a reclosable bag for our product

We have a logo, and we need to put it on packaging for our product and while we want the look to be simple, we want it to follow good design principles and also contain spaces for other product descriptions.

There will be 5 sizes at launch so I'd like 5 variations, one for each size.

I've included a few mockups of the type of bag that I made but they are all just rough ideas that I had.

I want the brand to look scientific and methodical and even a bit quirky, as in "wow this is a serious product but also a bit unusual."

```html
<!DOCTYPE html>
<html lang="en">
<head>
<meta charset="utf-8">
<title>KR7 Veil Lighting Pouch, 5 Meters</title>
<link rel="stylesheet" href="https://fonts.googleapis.com/css2?family=Barlow+Semi+Condensed:wght@500;700&display=swap">
<style>
  :root {
    --backdrop: #2b2c30;
    --pouch: #0c0c0d;
    --ink-light: #f4f4f2;
    --ink-dark: #0c0c0d;
  }
  html, body {
    margin: 0;
    padding: 0;
    width: 1200px;
    height: 833px;
    overflow: hidden;
    background: var(--backdrop);
  }
  .pouch-art {
    display: block;
    width: 1200px;
    height: 833px;
  }
  .pouch-body { fill: var(--pouch); }
  .band-light { fill: var(--ink-light); }
  .category-title {
    font-family: "Barlow Semi Condensed", sans-serif;
    font-weight: 500;
    font-size: 36px;
    fill: var(--ink-light);
  }
  .size-tag {
    font-family: "Barlow Semi Condensed", sans-serif;
    font-weight: 500;
    font-size: 13px;
    fill: var(--ink-light);
  }
  .spec-line {
    font-family: "Barlow Semi Condensed", sans-serif;
    font-weight: 700;
    font-size: 23px;
    fill: var(--ink-dark);
  }
  .product-name {
    font-family: "Barlow Semi Condensed", sans-serif;
    font-weight: 700;
    font-size: 420px;
    fill: var(--ink-light);
  }
  .length-label {
    font-family: "Barlow Semi Condensed", sans-serif;
    font-weight: 700;
    font-size: 60px;
    fill: var(--ink-dark);
  }
</style>
</head>
<body>
<svg class="pouch-art" viewBox="0 0 1200 833" xmlns="http://www.w3.org/2000/svg" aria-label="KR7 veil lighting pouch, extra large, 5 meters">
  <defs>
    <clipPath id="name-window">
      <rect x="350" y="380" width="493" height="264"/>
    </clipPath>
  </defs>

  <rect class="pouch-body" x="350" y="110" width="493" height="672" rx="4"/>

  <text class="category-title" x="454" y="270" textLength="282" lengthAdjust="spacing">VEIL LIGHTING</text>
  <text class="size-tag" x="514" y="288" textLength="159" lengthAdjust="spacing">EXTRA LARGUE</text>

  <polygon class="band-light" points="368,304 709,304 670,370 368,370"/>
  <polygon class="band-light" points="719,304 830,304 830,366 694,366"/>
  <text class="spec-line" x="404" y="340" textLength="238" lengthAdjust="spacingAndGlyphs">SIMULATED D65 CRI 90+</text>
  <text class="spec-line" x="389" y="361" textLength="263" lengthAdjust="spacingAndGlyphs">6500K WHITE VEIL LIGHTING</text>

  <g clip-path="url(#name-window)">
    <text class="product-name" x="332" y="668" textLength="540" lengthAdjust="spacingAndGlyphs">KR7</text>
  </g>

  <polygon class="band-light" points="404,648 553,648 514,710 404,710"/>
  <polygon class="band-light" points="563,648 783,648 783,710 524,710"/>
  <text class="length-label" x="571" y="701" textLength="209" lengthAdjust="spacingAndGlyphs">5 METERS</text>
</svg>
</body>
</html>
```